RWT Fittings Ltd Business Cards

We need a business card with our business logo. We provide window and door installations on high-rises in west coast British Colombia, Canada.

I would like my business information and details on one side of the card, and the other side the company name with logo

Target Market(s)

General Contractors

Industry/Entity Type

Construction

Contact Information for Business Card

one side i want my company name and logo in the dark theme logo that i provided

Requirements
Must have
• Marco Peltieri, 16045518293, RWTFittings@mailbox-demo.com, 1407-5194 Linden Row Burnaby BC, V5H 2K9, Owner & Manager

```html
<!DOCTYPE html>
<html lang="en">
<head>
<meta charset="utf-8">
<title>RWT Fittings Ltd – Business Cards</title>
<link rel="stylesheet" href="https://fonts.googleapis.com/css2?family=Open+Sans:wght@400;700&display=swap">
<style>
  :root {
    --stage: #3a3a3a;
    --card-black: #121212;
    --accent-blue: #27a9e1;
    --accent-grey: #8f8f8f;
    --text-white: #f2f2f2;
    --pattern-dark: #1a1a1a;
    --pattern-light: #262626;
  }
  * { margin: 0; padding: 0; box-sizing: border-box; }
  html, body { width: 1200px; height: 780px; overflow: hidden; }
  body {
    background: var(--stage);
    font-family: "Open Sans", Arial, sans-serif;
    display: flex;
    align-items: center;
    justify-content: center;
    gap: 40px;
  }
  .card {
    position: relative;
    width: 540px;
    height: 310px;
    border-radius: 4px;
    overflow: hidden;
    background: var(--card-black);
    box-shadow: 0 12px 30px rgba(0,0,0,0.45);
  }
  .card-shapes { position: absolute; inset: 0; }

  /* Front: contact side */
  .brand {
    position: absolute;
    left: 34px;
    top: 132px;
    display: flex;
    align-items: center;
    gap: 10px;
    white-space: nowrap;
  }
  .brand-mark {
    width: 20px;
    height: 20px;
    background: var(--accent-blue);
    flex: none;
  }
  .brand-name {
    color: var(--accent-blue);
    font-weight: 700;
    font-size: 20px;
    letter-spacing: 0.2px;
  }
  .divider {
    position: absolute;
    left: 272px;
    top: 74px;
    width: 1px;
    height: 162px;
    background: var(--accent-blue);
  }
  .contact {
    position: absolute;
    left: 292px;
    top: 80px;
    color: var(--text-white);
    white-space: nowrap;
  }
  .contact-name {
    color: var(--accent-blue);
    font-weight: 700;
    font-size: 21px;
    line-height: 1.15;
  }
  .contact-role {
    font-size: 14px;
    margin-bottom: 10px;
  }
  .contact-line {
    display: flex;
    align-items: center;
    gap: 6px;
    font-size: 12.5px;
    line-height: 1.7;
  }
  .contact-line svg { width: 12px; height: 12px; flex: none; }
  .contact-address {
    font-size: 12.5px;
    line-height: 1.45;
    margin-top: 8px;
  }

  /* Back: brand side */
  .back-pattern {
    position: absolute;
    inset: 0;
    background: linear-gradient(135deg, var(--pattern-light) 0%, var(--pattern-dark) 60%, var(--card-black) 100%);
  }
  .back-brand {
    position: absolute;
    inset: 0;
    display: flex;
    align-items: center;
    justify-content: center;
    gap: 12px;
  }
  .back-brand .brand-mark { width: 28px; height: 28px; }
  .back-brand .brand-name { font-size: 32px; }
</style>
</head>
<body>

  <section class="card card-front" aria-label="Business card, contact side">
    <svg class="card-shapes" viewBox="0 0 540 310" preserveAspectRatio="none" aria-hidden="true">
      <polygon points="0,0 230,0 0,150" fill="var(--accent-grey)"/>
      <polygon points="540,310 300,310 540,140" fill="var(--accent-blue)"/>
      <ellipse cx="262" cy="150" rx="330" ry="150" fill="var(--card-black)"/>
    </svg>

    <div class="brand">
      <span class="brand-mark"></span>
      <span class="brand-name">RWT Fittings Ltd</span>
    </div>

    <div class="divider"></div>

    <div class="contact">
      <p class="contact-name">Marco Peltieri</p>
      <p class="contact-role">Owner &amp; Manager</p>
      <p class="contact-line">
        <svg viewBox="0 0 24 24" aria-hidden="true"><path fill="var(--accent-blue)" d="M6.6 10.8a15.1 15.1 0 0 0 6.6 6.6l2.2-2.2a1 1 0 0 1 1-.25 11.4 11.4 0 0 0 3.6.57 1 1 0 0 1 1 1V20a1 1 0 0 1-1 1A17 17 0 0 1 3 4a1 1 0 0 1 1-1h3.5a1 1 0 0 1 1 1c0 1.25.2 2.450.57 3.57a1 1 0 0 1-.25 1z"/></svg>
        16045518293
      </p>
      <p class="contact-line">
        <svg viewBox="0 0 24 24" aria-hidden="true"><path fill="var(--accent-blue)" d="M3 5h18a1 1 0 0 1 1 1v12a1 1 0 0 1-1 1H3a1 1 0 0 1-1-1V6a1 1 0 0 1 1-1zm9 7.5L4 7.3V8l8 5.2L20 8v-.7z"/></svg>
        RWTFittings@mailbox-demo.com
      </p>
      <p class="contact-address">1407-5194 Linden Row<br>Burnaby BC, V5H 2K9</p>
    </div>
  </section>

  <section class="card card-back" aria-label="Business card, brand side">
    <div class="back-pattern" role="img" aria-label="Dark tone-on-tone repeating pattern of high-rise buildings with windows"></div>
    <div class="back-brand">
      <span class="brand-mark"></span>
      <span class="brand-name">RWT Fittings Ltd</span>
    </div>
  </section>

</body>
</html>
```